Ductless Mini Split Business Website

Copper Fern Services is looking to design an eye catching educational website about installing Ductless mini splits.

Similar to this company.
https://www.halvikstream.com/

Coding

Coded - Design and coding required

```html
<!DOCTYPE html>
<html lang="en">
<head>
<meta charset="utf-8">
<title>Copper Fern Services – Ductless Experts</title>
<link href="https://fonts.googleapis.com/css2?family=Roboto:wght@400;500;700;900&display=swap" rel="stylesheet">
<style>
:root{
  --yellow:#f8d20a;
  --ink:#1d1d1d;
  --text:#444;
  --white:#fff;
  --blush:#f3eeee;
  --line:#dcdcdc;
  --grey-bg:#e3e3e3;
}
*{box-sizing:border-box;margin:0;padding:0}
html,body{width:1200px;height:4963px;overflow:hidden}
body{position:relative;font-family:"Roboto",Arial,sans-serif;color:var(--text);background:var(--white)}
.abs{position:absolute}
.photo{position:absolute;display:block}
.btn{position:absolute;background:var(--yellow);color:var(--ink);font-weight:700;text-transform:uppercase;display:flex;align-items:center;justify-content:center;letter-spacing:.2px}
.sec-title{position:absolute;left:0;width:1200px;text-align:center;font-weight:700;font-size:29px;color:var(--ink);letter-spacing:.3px}
.bar{position:absolute;height:6px;width:60px;background:var(--yellow)}

/* header */
.brand{position:absolute;left:130px;top:22px;display:flex;align-items:center;gap:10px}
.brand-mark{width:34px;height:34px;border-radius:50%;background:var(--yellow)}
.brand-name{font-weight:700;font-size:21px;color:var(--ink)}
.brand-tag{position:absolute;left:132px;top:84px;font-weight:700;font-size:20px;color:var(--ink);letter-spacing:.3px}
.follow{position:absolute;left:652px;top:30px;display:flex;align-items:center;gap:7px;font-size:11px;font-weight:500;color:var(--ink)}
.dot{width:24px;height:24px;border-radius:50%;display:inline-block}
.d1{background:#3b5998}.d2{background:#1da1f2}.d3{background:#0e4f8a}
.callnow{position:absolute;left:862px;top:22px;display:flex;align-items:center;gap:10px}
.callnow small{display:block;font-size:11px;font-weight:500;color:var(--ink)}
.callnow b{display:block;font-size:24px;font-weight:500;color:var(--ink)}
.nav{position:absolute;left:422px;top:82px;display:flex;font-size:14px;font-weight:500;color:var(--ink)}
.nav a{color:inherit;text-decoration:none;padding:6px 11px;margin-right:10px}
.nav a.on{background:var(--yellow)}

/* hero */
.hero-photo{left:0;top:123px;width:1200px;height:574px;background:
  radial-gradient(ellipse 260px 120px at 490px 80px,rgba(255,255,255,.55),rgba(255,255,255,0)),
  radial-gradient(ellipse 140px 200px at 800px 450px,rgba(120,200,180,.55),rgba(120,200,180,0)),
  radial-gradient(ellipse 180px 150px at 1120px 500px,rgba(240,236,228,.8),rgba(240,236,228,0)),
  linear-gradient(180deg,#a6aeae 0%,#8c9596 40%,#66727a 56%,#4f5b65 72%,#5d6670 80%,#d9d3c7 90%,#ebe5d9 100%)}
.hero-title{position:absolute;left:792px;top:158px;font-weight:900;font-size:49px;line-height:50px;color:var(--white)}
.arrow-tab{position:absolute;width:34px;height:40px;background:var(--white);display:flex;align-items:center;justify-content:center}

/* welcome */
.welcome-kicker{position:absolute;left:693px;top:752px;font-size:24px;color:var(--ink)}
.welcome-title{position:absolute;left:693px;top:786px;font-size:30px;font-weight:700;color:var(--ink)}
.welcome-copy{position:absolute;left:695px;top:880px;width:374px;font-size:15.5px;line-height:22.5px;color:var(--text)}

/* services */
.svc{position:absolute;width:303px;height:297px}
.svc .photo{left:0;top:0;width:303px;height:297px}
.svc-cap{position:absolute;left:10px;bottom:-12px;width:283px;height:60px;background:var(--white);display:flex;align-items:center;justify-content:space-between;padding:0 18px 0 19px;box-shadow:0 2px 6px rgba(0,0,0,.08)}
.svc-cap span{font-size:13px;font-weight:500;color:var(--ink);line-height:16px;text-transform:uppercase}
.svc-cap i{font-style:normal;background:var(--yellow);font-size:12px;font-weight:700;color:var(--ink);padding:6px 10px}

/* why */
.why-panel{position:absolute;left:420px;top:2158px;width:408px;height:520px;background:var(--white)}
.why-title{position:absolute;left:38px;top:32px;font-size:29px;font-weight:700;color:var(--ink)}
.why-item{position:absolute;left:30px;width:350px;display:flex;gap:20px}
.why-icon{width:62px;height:62px;border-radius:50%;background:var(--yellow);flex:none;display:flex;align-items:center;justify-content:center}
.why-item h4{font-size:13.5px;font-weight:500;color:var(--ink);text-transform:uppercase;margin-bottom:6px;margin-top:2px}
.why-item p{font-size:13px;line-height:16px;color:var(--text)}
.why-line{position:absolute;left:30px;width:350px;height:1px;background:var(--line)}

/* blog */
.post{position:absolute;top:2830px;width:290px;height:415px;background:var(--white);box-shadow:0 0 14px rgba(0,0,0,.13)}
.post .photo{left:12px;top:14px;width:266px;height:212px}
.post h3{position:absolute;left:26px;top:254px;width:240px;font-size:14.5px;line-height:18px;font-weight:700;color:var(--ink);text-transform:uppercase}
.post p{position:absolute;left:26px;top:300px;width:240px;font-size:12.5px;line-height:15px;color:var(--text)}
.post .btn{left:26px;top:362px;width:96px;height:26px;font-size:11.5px}

/* testimonials */
.quote{position:absolute;top:3456px;width:373px;height:279px;background:var(--white);padding:32px 38px}
.stars{color:var(--yellow);font-size:13px;letter-spacing:2px}
.quote h4{font-size:13.5px;line-height:18px;font-weight:700;color:var(--ink);margin-top:8px}
.quote p{font-size:13px;line-height:19px;color:var(--text);margin-top:14px}
.quote .by{margin-top:16px;display:flex;align-items:center;gap:10px;font-size:12px;font-weight:500;color:var(--ink)}
.quote .by::before{content:"";width:26px;height:1px;background:#999}
.dots{position:absolute;left:550px;top:3783px;display:flex;gap:13px}
.dots span{width:9px;height:9px;border-radius:50%;background:var(--white)}
.dots span.on{background:var(--yellow)}

/* contact */
.form-panel{position:absolute;left:575px;top:4016px;width:488px;height:354px;background:var(--white);box-shadow:0 0 12px rgba(0,0,0,.1)}
.field{position:absolute;height:38px;border:1px solid #9d9d9d;font-size:11px;color:#555;padding:12px 14px;text-transform:uppercase}

/* footer */
.foot-brand{position:absolute;left:0;width:1200px;top:4583px;display:flex;justify-content:center;align-items:center;gap:12px}
.foot-brand .brand-mark{width:44px;height:44px}
.foot-brand .brand-name{font-size:30px}
.foot-tag{position:absolute;left:0;width:1200px;top:4637px;text-align:center;font-size:29px;font-weight:700;color:var(--ink)}
.foot-info{position:absolute;top:4703px;display:flex;align-items:center;gap:14px;font-size:14px;line-height:18px;color:var(--ink)}
.foot-ico{width:30px;height:30px;border-radius:50%;background:var(--yellow);display:flex;align-items:center;justify-content:center;flex:none}
.foot-rule{position:absolute;left:310px;width:570px;height:1px;background:var(--line)}
.foot-links{position:absolute;left:0;width:1200px;top:4805px;text-align:center;font-size:14px;color:var(--ink)}
.foot-follow{position:absolute;left:0;width:1200px;top:4846px;display:flex;justify-content:center;align-items:center;gap:8px;font-size:14px;color:var(--ink)}
.copy{position:absolute;left:0;width:1200px;top:4916px;text-align:center;font-size:12px;color:var(--ink)}
</style>
</head>
<body>

<header>
  <div class="brand"><span class="brand-mark"></span><span class="brand-name">Copper Fern Services</span></div>
  <div class="brand-tag">DUCTLESS EXPERTS</div>
  <div class="follow">FOLLOW US <span class="dot d1"></span><span class="dot d2"></span><span class="dot d3"></span></div>
  <div class="callnow">
    <svg width="34" height="34" viewBox="0 0 24 24" fill="none" stroke="#1d1d1d" stroke-width="1.8"><path d="M5 3h4l2 5-2.5 1.5a11 11 0 0 0 6 6L16 13l5 2v4a2 2 0 0 1-2 2A17 17 0 0 1 3 5a2 2 0 0 1 2-2z"/></svg>
    <div><small>CALL US NOW</small><b>888.888.8888</b></div>
  </div>
  <nav class="nav">
    <a class="on">HOME</a><a>ABOUT US</a><a>DUCTLESS HEAT PUMPS</a><a>REVIEWS</a><a>BLOG</a><a>CONTACT US</a>
  </nav>
</header>

<section>
  <div class="photo hero-photo" role="img" aria-label="Woman on a sofa cooling the room with a wall-mounted mini split remote"></div>
  <h1 class="hero-title">INSTALLING<br>DUCTLESS<br>MINI SPLITS</h1>
  <div class="btn" style="left:797px;top:325px;width:138px;height:44px;font-size:16px">Read More</div>
  <div class="arrow-tab" style="left:0;top:389px"><svg width="12" height="16" viewBox="0 0 12 16"><path d="M9 2 3 8l6 6" fill="none" stroke="#333" stroke-width="2"/></svg></div>
  <div class="arrow-tab" style="left:1166px;top:389px"><svg width="12" height="16" viewBox="0 0 12 16"><path d="M3 2l6 6-6 6" fill="none" stroke="#333" stroke-width="2"/></svg></div>
</section>

<section>
  <div class="photo" role="img" aria-label="Hand pointing a remote at an air conditioner" style="left:130px;top:746px;width:526px;height:410px;background:radial-gradient(ellipse 170px 110px at 150px 300px,rgba(214,176,150,.75),rgba(214,176,150,0)),radial-gradient(ellipse 150px 120px at 380px 220px,rgba(150,190,225,.55),rgba(150,190,225,0)),linear-gradient(120deg,#a9b0b4 0%,#c9cdcf 40%,#eef0f0 70%,#dfe2e3 100%)"></div>
  <div class="welcome-kicker">WELCOME TO</div>
  <h2 class="welcome-title">COPPER FERN SERVICES</h2>
  <div class="bar" style="left:694px;top:838px"></div>
  <p class="welcome-copy">Lorem ipsum dolor sit amet, consectetur adipi scing elit, sed do eiusmod tempor inci didunt ut labore et dolore magna aliqua. Ut enim ad minim veniam, quis nostrud exercitation ullamco laboris nisi ut aliquip ex ea commodo consequat. Duis aute irure dolor in reprehenderit in voluptate velit esse cillum dolore eu fugiat nulla pariatur. Excepteu lorem ipsum.</p>
  <div class="btn" style="left:698px;top:1101px;width:142px;height:44px;font-size:16px">Read More</div>
</section>

<section>
  <div class="abs" style="left:0;top:1208px;width:1200px;height:910px;background:var(--blush)"></div>
  <h2 class="sec-title" style="top:1251px">OUR SERVICES</h2>
  <div class="bar" style="left:570px;top:1301px"></div>

  <div class="svc" style="left:130px;top:1348px"><div class="photo" role="img" aria-label="Technician replacing a ceiling vent filter" style="background:radial-gradient(ellipse 120px 110px at 110px 200px,rgba(205,150,120,.8),rgba(205,150,120,0)),linear-gradient(150deg,#f2f0ec 0%,#dcd9d3 50%,#b9a89a 100%)"></div><div class="svc-cap"><span>Baseboard Heat<br>Replacement</span><i>MORE</i></div></div>
  <div class="svc" style="left:448px;top:1348px"><div class="photo" role="img" aria-label="Worker installing an outdoor mini split unit" style="background:radial-gradient(ellipse 60px 90px at 230px 130px,rgba(215,225,60,.85),rgba(215,225,60,0)),radial-gradient(ellipse 70px 60px at 80px 120px,rgba(235,235,232,.85),rgba(235,235,232,0)),linear-gradient(160deg,#858481 0%,#6d6c69 60%,#8a4a3a 100%)"></div><div class="svc-cap"><span>Ductless<br>Installation</span><i>MORE</i></div></div>
  <div class="svc" style="left:765px;top:1348px"><div class="photo" role="img" aria-label="Hands servicing an indoor unit with a screwdriver" style="background:radial-gradient(ellipse 90px 80px at 100px 200px,rgba(220,165,135,.85),rgba(220,165,135,0)),radial-gradient(ellipse 80px 60px at 230px 120px,rgba(215,150,120,.7),rgba(215,150,120,0)),linear-gradient(160deg,#5f7078 0%,#dfe3e5 45%,#f4f5f5 100%)"></div><div class="svc-cap"><span>Ductless<br>Maintenance</span><i>MORE</i></div></div>
  <div class="svc" style="left:130px;top:1683px"><div class="photo" role="img" aria-label="Technician repairing the circuit board of a unit" style="background:radial-gradient(ellipse 90px 70px at 60px 70px,rgba(160,40,35,.85),rgba(160,40,35,0)),radial-gradient(ellipse 70px 60px at 160px 150px,rgba(60,120,80,.7),rgba(60,120,80,0)),linear-gradient(150deg,#6e5544 0%,#a48c76 40%,#e6e4e0 75%,#cdbfae 100%)"></div><div class="svc-cap"><span>Ductless<br>Repair</span><i>MORE</i></div></div>
  <div class="svc" style="left:448px;top:1683px"><div class="photo" role="img" aria-label="Thermostat in a bright living room" style="background:radial-gradient(ellipse 55px 70px at 200px 200px,rgba(245,245,243,.95),rgba(245,245,243,0)),linear-gradient(180deg,#8e8e8c 0%,#a3a3a1 45%,#d8d6d2 65%,#c9c6c1 100%)"></div><div class="svc-cap"><span>Ductless<br>Warranty</span><i>MORE</i></div></div>
  <div class="svc" style="left:765px;top:1683px"><div class="photo" role="img" aria-label="Living room with a fireplace" style="background:radial-gradient(ellipse 40px 35px at 150px 200px,rgba(230,120,40,.95),rgba(230,120,40,0)),radial-gradient(ellipse 90px 80px at 150px 200px,rgba(60,55,50,.55),rgba(60,55,50,0)),linear-gradient(180deg,#f0eee9 0%,#e2ddd5 55%,#b8a998 100%)"></div><div class="svc-cap"><span>Whole House<br>Ductless</span><i>MORE</i></div></div>

  <div class="btn" style="left:511px;top:2035px;width:177px;height:45px;font-size:17px">More Services</div>
</section>

<section>
  <div class="photo" role="img" aria-label="Couple relaxing in a room cooled by a wall unit, with a bee mascot" style="left:0;top:2118px;width:1200px;height:560px;background:radial-gradient(ellipse 130px 160px at 180px 200px,rgba(120,200,235,.7),rgba(120,200,235,0)),radial-gradient(ellipse 90px 80px at 250px 360px,rgba(245,205,20,.55),rgba(245,205,20,0)),radial-gradient(ellipse 80px 60px at 1060px 240px,rgba(200,130,90,.65),rgba(200,130,90,0)),radial-gradient(ellipse 150px 150px at 1000px 460px,rgba(90,110,140,.6),rgba(90,110,140,0)),linear-gradient(90deg,#e6e8ea 0%,#d4d7da 35%,#cdc9c5 70%,#bdb5ad 100%)"></div>
  <div class="why-panel">
    <h2 class="why-title">WHY CHOOSE US</h2>
    <div class="why-item" style="top:100px">
      <span class="why-icon"><svg width="30" height="24" viewBox="0 0 30 24" fill="none" stroke="#1d1d1d" stroke-width="2"><rect x="2" y="3" width="24" height="17" rx="2"/><path d="M2 9h24"/></svg></span>
      <div><h4>0% Financing for 60 months</h4><p>Lorem ipsum dolor sit amet, conse ctetur adipi scing elit, sed do eiusmod tempor inci didunt ut labore.</p></div>
    </div>
    <div class="why-line" style="top:198px"></div>
    <div class="why-item" style="top:220px">
      <span class="why-icon"><svg width="26" height="26" viewBox="0 0 26 26" fill="none" stroke="#1d1d1d" stroke-width="2"><circle cx="13" cy="10" r="7"/><path d="M3 22h20"/></svg></span>
      <div><h4>365 Day, Money Back Guarentee</h4><p>Lorem ipsum dolor sit amet, conse ctetur adipi scing elit, sed do eiusmod tempor inci didunt ut labore.</p></div>
    </div>
    <div class="why-line" style="top:318px"></div>
    <div class="why-item" style="top:344px">
      <span class="why-icon"><svg width="26" height="28" viewBox="0 0 26 28" fill="#1d1d1d"><circle cx="13" cy="9" r="6"/><path d="M2 27c0-7 5-11 11-11s11 4 11 11z"/></svg></span>
      <div><h4>We are the experts in<br>ductless services</h4><p>Lorem ipsum dolor sit amet, conse ctetur adipi scing elit, sed do eiusmod tempor inci didunt ut labore.</p></div>
    </div>
  </div>
</section>

<section>
  <h2 class="sec-title" style="top:2727px">LATEST BLOG</h2>
  <div class="bar" style="left:570px;top:2775px"></div>
  <article class="post" style="left:128px"><div class="photo" role="img" aria-label="Technician installing an indoor unit" style="background:radial-gradient(ellipse 80px 90px at 90px 120px,rgba(205,150,120,.8),rgba(205,150,120,0)),radial-gradient(ellipse 60px 70px at 200px 70px,rgba(90,110,120,.6),rgba(90,110,120,0)),linear-gradient(135deg,#f3f2ef,#dcd8d2 60%,#c7beb4)"></div><h3>Lorem ipsum dolor sit a consectetur adipisc</h3><p>Lorem ipsum dolor sit amet, conse ctetur adipi scing elit, sed do eiusmod tempor incididunt.</p><div class="btn">Read More</div></article>
  <article class="post" style="left:456px"><div class="photo" role="img" aria-label="Family in a bright room with a wall unit" style="background:radial-gradient(ellipse 40px 80px at 215px 150px,rgba(120,140,190,.6),rgba(120,140,190,0)),linear-gradient(90deg,#c9d3dc 0%,#eef2f5 45%,#dfe6ec 100%)"></div><h3>Lorem ipsum dolor sit a consectetur adipisc</h3><p>Lorem ipsum dolor sit amet, conse ctetur adipi scing elit, sed do eiusmod tempor incididunt.</p><div class="btn">Read More</div></article>
  <article class="post" style="left:777px"><div class="photo" role="img" aria-label="Technician servicing a ceiling cassette" style="background:radial-gradient(ellipse 110px 60px at 170px 60px,rgba(240,242,244,.95),rgba(240,242,244,0)),radial-gradient(ellipse 80px 110px at 80px 150px,rgba(40,55,95,.9),rgba(40,55,95,0)),linear-gradient(135deg,#c9ced4,#e6e9ec)"></div><h3>Lorem ipsum dolor sit a consectetur adipisc</h3><p>Lorem ipsum dolor sit amet, conse ctetur adipi scing elit, sed do eiusmod tempor incididunt.</p><div class="btn">Read More</div></article>
</section>

<section>
  <div class="photo" role="img" aria-label="Dim open-plan kitchen and living room" style="left:0;top:3307px;width:1200px;height:525px;background:radial-gradient(ellipse 140px 120px at 1000px 150px,rgba(120,140,90,.55),rgba(120,140,90,0)),radial-gradient(ellipse 160px 100px at 150px 120px,rgba(170,150,130,.45),rgba(170,150,130,0)),linear-gradient(180deg,#4a3d35 0%,#34291f 45%,#2b211b 70%,#5a4535 100%)"></div>
  <h2 class="sec-title" style="top:3356px;color:var(--white)">TESTIMONIALS</h2>
  <div class="bar" style="left:570px;top:3404px"></div>
  <svg class="abs" style="left:133px;top:3588px" width="14" height="22" viewBox="0 0 14 22"><path d="M11 2 3 11l8 9" fill="none" stroke="#fff" stroke-width="2.5"/></svg>
  <svg class="abs" style="left:1050px;top:3588px" width="14" height="22" viewBox="0 0 14 22"><path d="M3 2l8 9-8 9" fill="none" stroke="#fff" stroke-width="2.5"/></svg>
  <div class="quote" style="left:215px"><div class="stars">★★★★★</div><h4>BUT I MUST EXPLAIN TO YOU HOW<br>ALL THIS MISTAKEN IDEA</h4><p>Sed ut perspiciatis unde omnis iste nat us error sit voluptatem accusantium dolore mque laudantium, totam rem aperi am, eaque ipsa quae ab illo inventore veritatis .</p><div class="by">RICHARD</div></div>
  <div class="quote" style="left:615px"><div class="stars">★★★★★</div><h4>BUT I MUST EXPLAIN TO YOU HOW<br>ALL THIS MISTAKEN IDEA</h4><p>Sed ut perspiciatis unde omnis iste nat us error sit voluptatem accusantium dolore mque laudantium, totam rem aperi am, eaque ipsa quae ab illo inventore veritatis .</p><div class="by">RICHARD</div></div>
  <div class="dots"><span></span><span></span><span class="on"></span><span></span><span></span></div>
</section>

<section>
  <div class="abs" style="left:0;top:3832px;width:1200px;height:740px;background:var(--grey-bg)"></div>
  <h2 class="sec-title" style="top:3880px">CONTACT US TODAY</h2>
  <div class="bar" style="left:570px;top:3928px"></div>
  <div class="photo" role="img" aria-label="Happy family walking together in a bright home" style="left:130px;top:3978px;width:608px;height:442px;background:radial-gradient(ellipse 70px 150px at 290px 250px,rgba(170,140,110,.6),rgba(170,140,110,0)),radial-gradient(ellipse 60px 140px at 140px 290px,rgba(200,170,140,.55),rgba(200,170,140,0)),radial-gradient(ellipse 45px 100px at 420px 330px,rgba(120,150,190,.55),rgba(120,150,190,0)),linear-gradient(180deg,#f6f5f2 0%,#ecebe7 60%,#d9d3c9 100%)"></div>
  <form class="form-panel">
    <div class="field" style="left:28px;top:32px;width:212px">First Name</div>
    <div class="field" style="left:253px;top:32px;width:212px">Last Name</div>
    <div class="field" style="left:28px;top:88px;width:212px">E mail ID</div>
    <div class="field" style="left:253px;top:88px;width:212px">Subject</div>
    <div class="field" style="left:28px;top:144px;width:437px;height:124px">Message</div>
    <div class="btn" style="left:28px;top:288px;width:120px;height:42px;font-size:17px">Subject</div>
  </form>
</section>

<footer>
  <svg class="abs" style="left:0;top:4540px" width="1200" height="60" viewBox="0 0 1200 60"><path d="M0 20 Q600 -4 1200 20 L1200 60 L0 60 Z" fill="#fff"/><path d="M0 20 Q600 -4 1200 20" fill="none" stroke="#f8d20a" stroke-width="3"/></svg>
  <div class="abs" style="left:0;top:4572px;width:1200px;height:391px;background:var(--white)"></div>
  <div class="foot-brand"><span class="brand-mark"></span><span class="brand-name">Copper Fern Services</span></div>
  <div class="foot-tag">DUCTLESS EXPERTS</div>
  <div class="foot-rule" style="top:4680px"></div>
  <div class="foot-info" style="left:310px"><span class="foot-ico"><svg width="12" height="16" viewBox="0 0 12 16"><path d="M6 1a5 5 0 0 1 5 5c0 4-5 9-5 9S1 10 1 6a5 5 0 0 1 5-5z" fill="#1d1d1d"/><circle cx="6" cy="6" r="2" fill="#f8d20a"/></svg></span><div>48 Tamsin Lane<br>Corvale, WI 53790</div></div>
  <div class="foot-info" style="left:532px"><span class="foot-ico"><svg width="14" height="14" viewBox="0 0 24 24" fill="#1d1d1d"><path d="M5 3h4l2 5-2.5 1.5a11 11 0 0 0 6 6L16 13l5 2v4a2 2 0 0 1-2 2A17 17 0 0 1 3 5a2 2 0 0 1 2-2z"/></svg></span><div>Call Us<br>888.888.8888</div></div>
  <div class="foot-info" style="left:716px"><span class="foot-ico"><svg width="14" height="11" viewBox="0 0 14 11"><rect x="0" y="0" width="14" height="11" rx="1" fill="#1d1d1d"/><path d="M1 1l6 5 6-5" fill="none" stroke="#f8d20a" stroke-width="1.3"/></svg></span><div>E mail Us<br>info@copperfernservices.com</div></div>
  <div class="foot-rule" style="top:4772px"></div>
  <div class="foot-links">Home &nbsp;| &nbsp;About Us &nbsp;| &nbsp;Ductless heat Pumps &nbsp;| &nbsp;Reviews &nbsp;| &nbsp;Blog &nbsp;| Contact Us</div>
  <div class="foot-follow">Follow us &nbsp;<span class="dot d1"></span><span class="dot d2"></span><span class="dot d3"></span></div>
  <div class="foot-rule" style="top:4888px"></div>
  <div class="copy">Copyright © 2020 All Rights Reserved</div>
</footer>

</body>
</html>
```